Business Card Design Project - 2 sided

We need a business card design for a card having one business on each side (ie. two businesses on one card). Would like a design that incorporates logo, tagline and normal fields (name, position, address, phone).

Would also like an allowance for small font text along the bottom (text to be determined, but less than 50 characters).

NB. Attached logo for Harbor Quill has two variations - either can be used.

www.harborquill-example.com / www.velmaro-example.com

```html
<!DOCTYPE html>
<html lang="en">
<head>
<meta charset="utf-8">
<title>Harbor Quill / Velmaro business card</title>
<link rel="stylesheet" href="https://fonts.googleapis.com/css2?family=Open+Sans:wght@400;600;700&display=swap">
<style>
  :root {
    --backdrop: #4a2c1a;
    --card: #ffffff;
    --ink: #3a3a3a;
    --rule: #8a8a8a;
    --navy: #27215f;
    --sky: #3a8ac4;
    --lime: #8cc63f;
    --white: #ffffff;
  }
  * { box-sizing: border-box; margin: 0; padding: 0; }
  html, body {
    width: 1200px; height: 412px; overflow: hidden;
    background: var(--backdrop);
    font-family: "Open Sans", Arial, sans-serif;
  }
  .stage { position: relative; width: 1200px; height: 412px; }
  .card {
    position: absolute; top: 65px; width: 497px; height: 284px;
    background: var(--card); overflow: hidden;
    box-shadow: 0 4px 10px rgba(0,0,0,.45);
  }
  .card--harbor { left: 75px; }
  .card--velmaro { left: 629px; }
  .card__swoosh { position: absolute; left: 0; top: 0; width: 497px; height: 284px; }
  .brand { position: absolute; left: 0; width: 276px; text-align: center; }
  .brand__name {
    display: inline-flex; align-items: center; gap: 8px;
    font-size: 27px; font-weight: 600; line-height: 1.2;
  }
  .brand__dot { width: 18px; height: 18px; border-radius: 50%; display: inline-block; background: var(--lime); }
  .brand__tagline { font-size: 10px; color: #111; margin-top: 6px; }
  .card--harbor .brand { top: 118px; }
  .card--harbor .brand__name { color: var(--navy); }
  .card--velmaro .brand { top: 115px; }
  .card--velmaro .brand__name { color: var(--sky); font-size: 30px; }
  .card--velmaro .brand__dot { width: 22px; height: 22px; }
  .card--velmaro .brand__tagline { font-size: 13px; font-weight: 700; color: #333; margin-top: 0; }
  .divider { position: absolute; left: 276px; top: 47px; width: 1px; height: 154px; background: var(--rule); }
  .contact { position: absolute; left: 305px; top: 49px; font-size: 12.5px; color: var(--ink); line-height: 16.5px; }
  .contact__line { display: flex; align-items: center; gap: 4px; }
  .contact__icon { width: 11px; height: 11px; fill: var(--ink); }
  .address { margin-top: 12px; }
  .note { margin-top: 11px; font-size: 11.5px; line-height: 13px; letter-spacing: -.3px; }
  .signature { position: absolute; right: 18px; bottom: 17px; color: var(--white); font-size: 16px; font-weight: 700; }
  .signature__title { font-size: 12.5px; font-weight: 400; }
</style>
</head>
<body>
<svg width="0" height="0" style="position:absolute" aria-hidden="true">
  <defs>
    <symbol id="icon-phone" viewBox="0 0 12 12"><path d="M2.5 1l2 2-1 1.3c.6 1.4 1.8 2.6 3.2 3.2L8 6.5l2 2-1.3 1.8C5 10.3 1.7 7 1 3.3z"/></symbol>
    <symbol id="icon-mobile" viewBox="0 0 12 12"><path d="M3.5 0.5h5v11h-5zM4.5 1.5v7h3v-7z"/></symbol>
    <symbol id="icon-fax" viewBox="0 0 12 12"><path d="M1 4h10v6H1zM3 1h6v3H3zM3 6h6v1H3z"/></symbol>
    <symbol id="icon-mail" viewBox="0 0 12 12"><path d="M1 3h10v7H1zM1 3l5 4 5-4"/></symbol>
  </defs>
</svg>

<main class="stage">
  <section class="card card--harbor" aria-label="Harbor Quill side">
    <svg class="card__swoosh" viewBox="0 0 497 284" aria-hidden="true">
      <path d="M0 212 C120 285 300 262 497 218 L497 284 L0 284Z" fill="var(--navy)"/>
      <path d="M0 222 C130 282 320 256 497 228" fill="none" stroke="var(--white)" stroke-width="2.5"/>
      <path d="M60 238 C190 272 330 236 430 220 C330 246 200 278 60 238Z" fill="var(--lime)"/>
    </svg>
    <div class="brand">
      <div class="brand__name"><span class="brand__dot"></span>Harbor Quill</div>
      <p class="brand__tagline">Website Translation and Localisation Specialist...</p>
    </div>
    <div class="divider"></div>
    <div class="contact">
      <p class="contact__line"><svg class="contact__icon"><use href="#icon-phone"/></svg>123-456-7890</p>
      <p class="contact__line"><svg class="contact__icon"><use href="#icon-mobile"/></svg>123-456-7890</p>
      <p class="contact__line"><svg class="contact__icon"><use href="#icon-fax"/></svg>123-456-7890</p>
      <p class="contact__line"><svg class="contact__icon"><use href="#icon-mail"/></svg>name@website.com</p>
      <p class="address">Complex name, Street name<br>City, State, zip code</p>
      <p class="note">xxxxxxxxxxxxxxxxxxxxxxxxxx<br>xxxxxxxxxxxxxxxxxxxxxxxxxx</p>
    </div>
    <p class="signature">Your Name <span class="signature__title">/ Title</span></p>
  </section>

  <section class="card card--velmaro" aria-label="Velmaro side">
    <svg class="card__swoosh" viewBox="0 0 497 284" aria-hidden="true">
      <path d="M0 212 C120 285 300 262 497 218 L497 284 L0 284Z" fill="var(--sky)"/>
      <path d="M0 222 C130 282 320 256 497 228" fill="none" stroke="var(--white)" stroke-width="2.5"/>
      <path d="M60 238 C190 272 330 236 430 220 C330 246 200 278 60 238Z" fill="var(--lime)"/>
    </svg>
    <div class="brand">
      <div class="brand__name"><span class="brand__dot"></span>Velmaro LLC</div>
      <p class="brand__tagline">Professional SEO Services</p>
    </div>
    <div class="divider"></div>
    <div class="contact">
      <p class="contact__line"><svg class="contact__icon"><use href="#icon-phone"/></svg>123-456-7890</p>
      <p class="contact__line"><svg class="contact__icon"><use href="#icon-mobile"/></svg>123-456-7890</p>
      <p class="contact__line"><svg class="contact__icon"><use href="#icon-fax"/></svg>123-456-7890</p>
      <p class="contact__line"><svg class="contact__icon"><use href="#icon-mail"/></svg>name@website.com</p>
      <p class="address">Complex name, Street name<br>City, State, zip code</p>
      <p class="note">xxxxxxxxxxxxxxxxxxxxxxxxxx<br>xxxxxxxxxxxxxxxxxxxxxxxxxx</p>
    </div>
    <p class="signature">Your Name <span class="signature__title">/ Title</span></p>
  </section>
</main>
</body>
</html>
```